Harborline Auto LLC

Car Dealer Customer Service
Address: 2874 Cresthaven Road, Marrowfield, QX 00481
web: www.harborlineautoxq.net
email: harborlineautoxq@mailnest.example
Phone: (555) 555-0148
Phone: (555) 555-0173

```html
<!DOCTYPE html>
<html lang="en">
<head>
<meta charset="utf-8">
<title>Harborline Auto – Business Card</title>
<link href="https://fonts.googleapis.com/css2?family=Poppins:wght@400;600&family=Roboto+Condensed:wght@700&display=swap" rel="stylesheet">
<style>
  :root {
    --backdrop: #2b2b2c;
    --card: #232425;
    --card-edge: #2c2d2f;
    --emboss: #161718;
    --blue: #2489c6;
    --gold: #e0a93a;
    --text: #e9e9e9;
  }
  * { margin: 0; padding: 0; box-sizing: border-box; }
  html, body { width: 1200px; height: 1138px; overflow: hidden; background: var(--backdrop); }
  body { position: relative; font-family: "Poppins", sans-serif; color: var(--text); }

  .card {
    position: absolute;
    width: 620px; height: 375px;
    border-radius: 16px;
    background: linear-gradient(160deg, var(--card-edge), var(--card) 60%);
    overflow: hidden;
    text-align: center;
  }
  .card--front { left: 274px; top: 186px; }
  .card--back  { left: 276px; top: 607px; }

  /* front */
  .front-mark {
    position: absolute; left: 0; right: 0; top: 96px;
    display: flex; flex-direction: column; align-items: center; gap: 18px;
  }
  .front-mark__dot { width: 84px; height: 84px; border-radius: 50%; background: var(--emboss); }
  .front-mark__name { font-weight: 600; font-size: 34px; letter-spacing: 1px; color: var(--emboss); text-transform: uppercase; }
  .front-web {
    position: absolute; left: 0; right: 0; top: 332px;
    display: flex; justify-content: center; align-items: center; gap: 24px;
    font-size: 15px;
  }
  .front-web__rule { width: 56px; height: 2px; background: var(--gold); }

  /* back */
  .brand { position: absolute; left: 0; right: 0; top: 44px; display: flex; flex-direction: column; align-items: center; }
  .brand__dot { width: 110px; height: 110px; border-radius: 50%; background: var(--blue); }
  .brand__name { margin-top: 18px; font-weight: 600; font-size: 30px; letter-spacing: 1px; color: var(--blue); text-transform: uppercase; line-height: 1; }
  .tagline { position: absolute; left: 0; right: 0; top: 226px; font-size: 15.5px; }
  .phones { position: absolute; left: 0; right: 0; top: 252px; display: flex; justify-content: center; gap: 16px; }
  .phone { display: flex; align-items: center; gap: 12px; font-family: "Roboto Condensed", sans-serif; font-weight: 700; font-size: 33px; color: var(--blue); }
  .phone svg { width: 28px; height: 28px; }
  .address { position: absolute; left: 0; right: 0; top: 294px; font-size: 15px; }
  .links { position: absolute; left: 0; right: 0; top: 315px; font-size: 15px; }
  .links__sep { margin: 0 8px; }
  .stripe { position: absolute; left: 0; right: 0; bottom: 0; height: 17px; display: flex; }
  .stripe__blue { flex: 1; background: var(--blue); }
  .stripe__gold { flex: 1; background: var(--gold); }
</style>
</head>
<body>
  <section class="card card--front">
    <div class="front-mark">
      <div class="front-mark__dot"></div>
      <div class="front-mark__name">Harborline Auto</div>
    </div>
    <div class="front-web">
      <span class="front-web__rule"></span>
      <span>www.harborlineautoxq.net</span>
      <span class="front-web__rule"></span>
    </div>
  </section>

  <section class="card card--back">
    <div class="brand">
      <div class="brand__dot"></div>
      <div class="brand__name">Harborline Auto</div>
    </div>
    <p class="tagline">Car Dealer Customer Service</p>
    <div class="phones">
      <div class="phone">
        <svg viewBox="0 0 28 28" aria-hidden="true"><circle cx="14" cy="14" r="12" fill="none" stroke="#e0a93a" stroke-width="2.4"/><path d="M10 8.5l2 0 1.2 3.2-1.5 1.2c.8 1.7 2 2.9 3.6 3.6l1.2-1.5 3.2 1.2 0 2c0 .8-.7 1.4-1.5 1.3C12.5 19 9 15.5 8.7 10c0-.8.5-1.5 1.3-1.5z" fill="#e0a93a"/></svg>
        <span>555-555-0148</span>
      </div>
      <div class="phone">
        <svg viewBox="0 0 28 28" aria-hidden="true"><circle cx="14" cy="14" r="12" fill="none" stroke="#e0a93a" stroke-width="2.4"/><path d="M10 8.5l2 0 1.2 3.2-1.5 1.2c.8 1.7 2 2.9 3.6 3.6l1.2-1.5 3.2 1.2 0 2c0 .8-.7 1.4-1.5 1.3C12.5 19 9 15.5 8.7 10c0-.8.5-1.5 1.3-1.5z" fill="#e0a93a"/></svg>
        <span>555-555-0173</span>
      </div>
    </div>
    <p class="address">2874 Cresthaven Road, Marrowfield, QX 00481</p>
    <p class="links">www.harborlineautoxq.net<span class="links__sep">|</span>harborlineautoxq@mailnest.example</p>
    <div class="stripe"><span class="stripe__blue"></span><span class="stripe__gold"></span></div>
  </section>
</body>
</html>
```